Health and Fitness Club requires a stunning and simple website

We are a health and fitness club based in Dubai, when we launch we will be the biggest club in the country, we will also have the 2 largest activity rooms in the country, we are setting a new standard in the industry by offering one thing, our attitude.

Our attitude means the following:
unlike other clubs we have no hidden charges or fees
our members can join daily, monthly, 6 months or annually
our service and facility are comparable to 5* hotel gyms
our equipment is second to none
our space is the biggest in the country
we do not force our members to use our in-house personal trainers - you can bring your own and we will not charge them entry!
we will have a cutting edge brawnmesh box in our gym with classes by the best trainers in the country
we will be providing free-lance personal trainers a platform to engage customers, grow their business and even use our activity rooms for classes

Basically we will be a gym like no other, simply because we are gym people and we hate the restrictive practices and hidden charges by other gyms, so we are making our own gym which focuses on quality and service.

All of this has to be communicated in the style of the website, the colors of the website we want to be limited to the logo colors as this will be the same theme running throughout the gym.

The landing page of the website HAS to incorporate elements from our social media presences, this basically is the usual, chirplo, snapvault, kinwall. We can have these as a sidebar, the centre of the page should display the latest article from our blog (also on the website) Also we need to have a calendar for activities and classes on the front page. The menu should have links to the following:
Latest News
About us
Team
Gallery
Membership
Classes
Member Log In
Contact Us
Location

The style of the website has to be similar to the logo, particularly in terms of the fonts used.

```html
<!DOCTYPE html>
<html lang="en">
<head>
<meta charset="utf-8">
<title>Ironhold Health &amp; Fitness Club</title>
<link href="https://fonts.googleapis.com/css2?family=Oswald:wght@300;400;500&family=Open+Sans:ital,wght@0,400;0,600;0,700;1,400;1,700&display=swap" rel="stylesheet">
<style>
:root{
  --red:#b31e2a;
  --red-dark:#8e1620;
  --ink:#222;
  --dark:#1d1d1d;
  --footer:#2c2c2c;
  --grey-band:#e7e7e7;
  --panel:#ececec;
  --muted:#8a8a8a;
  --line:#d4d4d4;
  --white:#fff;
  --head:'Oswald',sans-serif;
  --body:'Open Sans',sans-serif;
}
*{box-sizing:border-box;margin:0;padding:0}
html,body{width:1200px;height:3203px;overflow:hidden}
body{position:relative;background:var(--white);font-family:var(--body);color:var(--ink);font-size:13px}
.abs{position:absolute}
ul{list-style:none}
.h2{font-family:var(--head);font-weight:400;font-size:26px;color:var(--ink);letter-spacing:-.2px}
.h2 em{font-style:normal;color:var(--red)}

/* hero + header */
.hero{left:0;top:0;width:1200px;height:679px;background:linear-gradient(100deg,#2a2a2a 0%,#4a4a4a 38%,#777 55%,#3a3a3a 75%,#111 100%)}
.header-shade{left:0;top:0;width:1200px;height:165px;background:linear-gradient(#0c0c0c 0%,rgba(12,12,12,.75) 70%,rgba(12,12,12,0))}
.brand{left:100px;top:46px;display:flex;align-items:center;gap:12px;font-family:var(--head);font-size:28px;font-weight:500;color:var(--white);letter-spacing:1px}
.brand i{width:40px;height:40px;border-radius:50%;background:var(--red);display:block}
.callus{left:626px;top:40px;display:flex;align-items:center;gap:10px;font-family:var(--head);font-size:20px;color:#ddd}
.callus b{color:var(--red);font-weight:400}
.btn-login{left:871px;top:41px;width:119px;height:31px;background:var(--red);color:#fff;font-family:var(--head);font-size:14px;display:flex;align-items:center;justify-content:center}
.btn-signup{left:1008px;top:41px;width:92px;height:31px;background:#8d8d8d;color:#fff;font-family:var(--head);font-size:14px;display:flex;align-items:center;justify-content:center}
.nav{left:360px;top:118px;width:750px;display:flex;justify-content:space-between;font-family:var(--head);font-size:16px;color:#eee}
.nav .active{color:var(--red);border-bottom:2px solid var(--red);padding-bottom:10px}
.caption{left:102px;top:305px;width:538px;height:229px;background:rgba(120,25,32,.55);padding:16px 14px;color:#fff}
.caption h1{font-family:var(--head);font-weight:400;font-size:38px;line-height:1.1}
.caption h3{font-family:var(--head);font-weight:300;font-size:24px;margin-top:6px}
.caption p{font-size:13px;line-height:1.35;margin-top:6px;color:#eee}
.readmore{left:301px;top:480px;width:141px;height:36px;border:1px solid #ddd;color:#fff;font-size:11px;font-weight:600;display:flex;align-items:center;justify-content:center;letter-spacing:.5px}
.arrow{top:380px;width:46px;height:46px;background:#1a1a1a;display:flex;align-items:center;justify-content:center}
.arrow.next{left:1154px;background:var(--red-dark)}
.dots{left:570px;top:700px;display:flex;gap:12px}
.dots i{width:12px;height:12px;background:var(--dark);display:block}
.dots i:first-child{background:var(--red)}

/* about */
.about-h{left:100px;top:795px}
.portrait{left:100px;top:860px;width:122px;height:122px;background:linear-gradient(#9a9a9a,#3c3c3c)}
.about-side{left:248px;top:856px;width:292px;font-size:12.5px;line-height:1.45;color:#555;text-align:justify}
.about-more{left:100px;top:994px;width:440px;font-size:12.5px;line-height:1.45;color:#555}
.att-h{left:583px;top:795px}
.att-list{left:583px;top:860px;width:517px;font-size:12.5px;line-height:21px;color:#555}
.att-list li{position:relative;padding-left:32px}
.att-list li::before{content:"";position:absolute;left:4px;top:8px;width:7px;height:7px;border-radius:50%;background:#aaa}

/* grey band */
.band{left:0;top:1146px;width:1200px;height:342px;background:var(--grey-band)}
.col-h{top:1166px;text-align:center}
.trainers{left:96px;top:1228px;width:316px;height:213px;background:#fff}
.trainer{top:24px;width:120px;text-align:center}
.trainer .ph{width:66px;height:66px;border-radius:50%;margin:0 auto;background:linear-gradient(#aaa,#444)}
.trainer h4{font-size:11px;font-weight:700;margin-top:10px}
.trainer .role{font-size:9px;color:#3ca0d0;margin-top:2px}
.trainer p{font-size:10px;color:#555;margin-top:6px;line-height:1.3}
.trainer .icons{display:flex;justify-content:space-between;margin:10px 10px 0;font-size:11px}
.tdiv{left:158px;top:24px;width:1px;height:160px;background:var(--line)}
.events{left:440px;top:1228px;width:318px;height:213px;background:var(--dark);color:#fff;padding:12px 14px}
.event{display:flex;gap:10px;height:94px}
.event + .event{border-top:1px solid #444;padding-top:10px}
.event .date{font-family:var(--head);font-size:15px;width:116px}
.event .thumb{width:108px;height:52px;background:linear-gradient(90deg,#555,#222);margin-top:6px}
.event .info{font-size:9px;color:#bbb;line-height:1.3;padding-top:2px}
.event .info .t{color:var(--red)}
.event .info h5{font-family:var(--head);font-weight:400;color:#fff;font-size:17px;margin:2px 0}
.event .info .bk{color:var(--red);font-weight:700;font-size:8px;margin-top:6px;text-align:center}
.blog{left:784px;top:1228px;width:318px;height:213px;background:#d6d6d6;padding:10px}
.post{display:flex;gap:14px;height:64px}
.post .thumb{width:56px;height:56px;background:linear-gradient(#8a7a6a,#3a3028)}
.post p{font-size:10.5px;color:#555;line-height:1.3}
.post small{display:block;font-size:10px;color:#777;margin-top:2px}

/* gallery / partners */
.gal-h{left:100px;top:1575px;width:696px;text-align:center}
.gallery{left:100px;top:1637px;width:696px;display:grid;grid-template-columns:repeat(3,231px);grid-auto-rows:151px;gap:2px 1.5px}
.gallery div{background:linear-gradient(135deg,#6d7f8e,#c3ccd3)}
.gallery div:nth-child(2n){background:linear-gradient(135deg,#c8d6de,#5f6f79)}
.partners-h{left:864px;top:1575px;width:236px;text-align:center}
.partners{left:868px;top:1680px;width:232px;display:grid;grid-template-columns:repeat(2,100px);column-gap:32px;row-gap:64px}
.partners span{height:38px;background:#d3d3d3;border-radius:4px;display:block}

/* classes / calendar */
.cls-h{left:100px;top:2021px}
.classes{left:100px;top:2081px;width:541px;height:300px;background:var(--panel);padding:18px 22px}
.class-row{display:flex;align-items:center;height:72px;border-bottom:1px solid var(--line);font-size:15px;color:#999;letter-spacing:.3px}
.class-row:last-child{border-bottom:0}
.class-row .nm{flex:1;display:flex;align-items:center;gap:10px}
.class-row .tools{display:flex;gap:30px;margin-right:10px}
.cal-head{left:690px;top:2003px;width:410px;height:72px;background:var(--red);color:#fff;font-family:var(--head);font-size:24px;display:flex;align-items:center;justify-content:space-between;padding:0 24px}
.cal-body{left:690px;top:2075px;width:410px;height:310px;background:var(--panel);padding:24px 20px;display:grid;grid-template-columns:repeat(7,1fr);grid-auto-rows:50px;text-align:center;font-family:var(--head);font-weight:300;font-size:21px;color:#999}
.cal-body .today{color:#2e8b3a;font-weight:500}
.cal-body .off{color:#ccc}

/* map + hours */
.map{left:0;top:2449px;width:1200px;height:444px;background:linear-gradient(135deg,#e4e1d9,#d9d6cc 50%,#e7e4dc)}
.pin{left:405px;top:2540px}
.hours{left:773px;top:2449px;width:327px;height:444px;background:var(--red);color:#fff;padding:22px 20px 16px}
.hours h3{font-family:var(--head);font-weight:300;font-size:26px;text-align:center;line-height:38px}
.hours h3 b{font-weight:400}
.hours ul{margin-top:12px}
.hours li{display:flex;align-items:center;height:34px;border-bottom:1px solid rgba(255,255,255,.25);font-size:11.5px;font-weight:600}
.hours li span:nth-child(2){flex:1;margin-left:10px}
.hours p{text-align:center;font-size:13px;line-height:1.4;margin-top:20px}
.hours .enjoy{font-size:24px;font-weight:700;font-style:italic;margin-top:8px;line-height:1.3}

/* footer */
.footer{left:0;top:2893px;width:1200px;height:263px;background:var(--footer);color:#bbb}
.f-h{font-family:var(--head);font-size:16px;color:#fff;letter-spacing:.3px}
.news{left:100px;top:2938px;width:300px;color:#bbb}
.news p{font-size:11px;line-height:1.35;margin-top:16px;text-transform:uppercase;color:#bbb}
.news .field{width:297px;height:30px;background:#9a9a9a;margin-top:16px;color:var(--red);font-size:10px;padding:8px 18px}
.news .submit{width:190px;height:30px;background:#d9424a;margin-top:10px;color:#fff;font-size:11px;display:flex;align-items:center;justify-content:center}
.f-brand{left:453px;top:2906px;width:305px;display:flex;align-items:center;justify-content:center;gap:10px;font-family:var(--head);font-size:22px;color:#fff;font-weight:500}
.f-brand i{width:32px;height:32px;border-radius:50%;background:var(--red);display:block}
.contact{left:453px;top:2960px;width:320px;font-size:12.5px;line-height:1.5;color:#aaa}
.contact .line{margin-top:12px;display:flex;align-items:center;gap:16px;color:#fff;font-size:11px}
.contact .line em{font-size:17px;color:#999}
.menu{left:826px;top:2938px;color:#bbb}
.community{left:1003px;top:2938px;color:#bbb}
.menu ul,.community ul{margin-top:14px;font-size:11px;line-height:21px;color:#bbb}
.menu li::before,.community li::before{content:"› ";color:#fff}
.bottom{left:0;top:3156px;width:1200px;height:47px;background:var(--red);color:#fff;font-size:12px;display:flex;align-items:center;justify-content:space-between;padding:0 100px}
.social{display:flex;gap:14px;font-size:11px}
</style>
</head>
<body>

<div class="abs hero" role="img" aria-label="Black and white photo of an athlete in a push-up stance"></div>
<div class="abs header-shade"></div>
<div class="abs brand"><i></i>IRONHOLD</div>
<div class="abs callus">
  <svg width="16" height="24" viewBox="0 0 16 24"><path d="M4 1h4l1 6-3 2c1 3 2 5 4 7l3-2 3 4-3 4c-6-2-11-10-11-19z" fill="#ddd"/></svg>
  Call us - <b>040 - 5512 - 73</b>
</div>
<div class="abs btn-login">Member Log-in</div>
<div class="abs btn-signup">Sign up</div>
<nav class="abs nav">
  <span class="active">Latest News</span><span>About us</span><span>Team</span><span>Gallery</span><span>Membership</span><span>Classes</span><span>Contact Us</span><span>Location</span>
</nav>

<div class="abs caption">
  <h1>PERFECT GYM</h1>
  <h3>BEST CHOISE FOR HEALTH FITNESS</h3>
  <p>Basically we will be a gym like no other, simply because we are gym people and we hate the restrictive practices and hidden charges by other gyms, so we are making our own gym which focuses on quality and service.</p>
</div>
<div class="abs readmore">READ MORE</div>
<div class="abs arrow" style="left:0"><svg width="14" height="18"><path d="M11 2L3 9l8 7" stroke="#fff" stroke-width="3" fill="none"/></svg></div>
<div class="abs arrow next"><svg width="14" height="18"><path d="M3 2l8 7-8 7" stroke="#fff" stroke-width="3" fill="none"/></svg></div>
<div class="abs dots"><i></i><i></i><i></i></div>

<h2 class="abs h2 about-h">About <em>Us</em></h2>
<div class="abs portrait" role="img" aria-label="Portrait photo of the club founder"></div>
<p class="abs about-side">Long established fact that a reader will be distracted by the readable content of a page when looking at its layout. The point of using Lorem Ipsum is that it has a more-or-less normal distribution of letters, as opposed to using 'Content here, content here', making it look like readable English.</p>
<p class="abs about-more">Many desktop publishing packages and web page editors now use Lorem Ipsum as their default model text, and a search for 'lorem ipsum' will uncover many web sites still in their infancy. Various versions have evolved over the years, sometimes by a</p>

<h2 class="abs h2 att-h">Our <em>Attitude</em></h2>
<ul class="abs att-list">
  <li>Unlike other clubs we have no hidden charges or fees</li>
  <li>Our members can join daily, monthly, 6 months or annually</li>
  <li>Our service and facility are comparable to 5* hotel gyms</li>
  <li>Our equipment is second to none</li>
  <li>Our space is the biggest in the country</li>
  <li>We do not force our members to use our in-house personal trainers - you can bring your own and we will not charge them entry!</li>
  <li>We will have a cutting edge brawnmesh box in our gym with classes by the best trainers in the country</li>
  <li>We will be providing free-lance personal trainers a platform to engage customers, grow their business and even use our activity rooms for classes</li>
</ul>

<div class="abs band"></div>
<h2 class="abs h2 col-h" style="left:96px;width:316px">Our <em>Trainers</em></h2>
<h2 class="abs h2 col-h" style="left:440px;width:318px">Next <em>Events</em></h2>
<h2 class="abs h2 col-h" style="left:784px;width:318px">From the <em>Blog</em></h2>

<div class="abs trainers">
  <svg class="abs" style="left:8px;top:90px" width="10" height="18"><path d="M8 2L2 9l6 7" stroke="#c44" stroke-width="1.5" fill="none"/></svg>
  <svg class="abs" style="left:298px;top:90px" width="10" height="18"><path d="M2 2l6 7-6 7" stroke="#999" stroke-width="1.5" fill="none"/></svg>
  <div class="abs trainer" style="left:28px">
    <div class="ph" role="img" aria-label="Trainer portrait"></div>
    <h4>MAYA RIVERS</h4><div class="role">SPINNING</div>
    <p>Creating the perfect body is no small</p>
    <div class="icons"><span style="color:#c33">♥ ✚</span><span style="color:#3ca0d0">✓ ✦</span></div>
  </div>
  <div class="abs tdiv"></div>
  <div class="abs trainer" style="left:168px">
    <div class="ph" role="img" aria-label="Trainer portrait"></div>
    <h4>OMAR GRANT</h4><div class="role">KIK BOXING</div>
    <p>Creating the perfect body is no small</p>
    <div class="icons"><span style="color:#999">♥ ✚</span><span style="color:#3ca0d0">✓ ✦</span></div>
  </div>
</div>

<div class="abs events">
  <div class="event">
    <div><div class="date">26 GEN, 2014</div><div class="thumb" role="img" aria-label="Aerobics class photo"></div></div>
    <div class="info"><span class="t">9.12.00 - 6.15.00</span><h5>AEROBICS</h5>Lorem ipsum dolor sit amet, consectetur adipiscing elit<div class="bk">BOOKING</div></div>
  </div>
  <div class="event">
    <div><div class="date">26 GEN, 2014</div><div class="thumb" role="img" aria-label="Spinning class photo"></div></div>
    <div class="info"><span class="t">9.12.00 - 6.15.00</span><h5>SPINNING</h5>Lorem ipsum dolor sit amet, consectetur adipiscing elit<div class="bk">BOOKING</div></div>
  </div>
</div>

<div class="abs blog">
  <div class="post"><div class="thumb" role="img" aria-label="Blog photo"></div><p>Lorem ipsum dolor sit amet, consectetur adipiscing elit<small>26 May, 2013</small></p></div>
  <div class="post"><div class="thumb" role="img" aria-label="Blog photo"></div><p>Lorem ipsum dolor sit amet, consectetur adipiscing elit<small>26 May, 2013</small></p></div>
  <div class="post"><div class="thumb" role="img" aria-label="Blog photo"></div><p>Lorem ipsum dolor sit amet, consectetur adipiscing elit<small>26 May, 2013</small></p></div>
</div>

<h2 class="abs h2 gal-h">Our <em>Gallery</em></h2>
<div class="abs gallery">
  <div role="img" aria-label="Gym floor with machines"></div>
  <div role="img" aria-label="Woman on a cross trainer"></div>
  <div role="img" aria-label="Row of treadmills"></div>
  <div role="img" aria-label="Woman training her back"></div>
  <div role="img" aria-label="Dumbbell rack"></div>
  <div role="img" aria-label="Spinning class"></div>
</div>
<h2 class="abs h2 partners-h">Our <em>Partners</em></h2>
<div class="abs partners"><span></span><span></span><span></span><span></span><span></span><span></span></div>

<h2 class="abs h2 cls-h">All <em>Classes</em></h2>
<div class="abs classes">
  <div class="class-row"><span class="nm"><svg width="14" height="14"><circle cx="7" cy="7" r="6" fill="#aaa"/><path d="M7 3v4h3" stroke="#fff" stroke-width="1.5" fill="none"/></svg>CARDIO FITNESS</span><span class="tools"><span>▦</span><span>✉</span><span>♡</span><span>➦</span></span></div>
  <div class="class-row"><span class="nm"><svg width="14" height="14"><circle cx="7" cy="7" r="6" fill="#aaa"/><path d="M7 3v4h3" stroke="#fff" stroke-width="1.5" fill="none"/></svg>SPINNING</span><span class="tools"><span>▦</span><span>✉</span><span>♡</span><span>➦</span></span></div>
  <div class="class-row"><span class="nm"><svg width="14" height="14"><circle cx="7" cy="7" r="6" fill="#aaa"/><path d="M7 3v4h3" stroke="#fff" stroke-width="1.5" fill="none"/></svg>PILATES</span><span class="tools"><span>▦</span><span>✉</span><span>♡</span><span>➦</span></span></div>
  <div class="class-row"><span class="nm"><svg width="14" height="14"><circle cx="7" cy="7" r="6" fill="#aaa"/><path d="M7 3v4h3" stroke="#fff" stroke-width="1.5" fill="none"/></svg>BOXING</span><span class="tools"><span>▦</span><span>✉</span><span>♡</span><span>➦</span></span></div>
</div>

<div class="abs cal-head">APRIL 2013
  <svg width="34" height="34" viewBox="0 0 34 34"><rect x="2" y="5" width="30" height="27" fill="#fff"/><rect x="8" y="1" width="3" height="8" fill="#fff"/><rect x="23" y="1" width="3" height="8" fill="#fff"/><g fill="#b31e2a"><rect x="6" y="13" width="5" height="5"/><rect x="14" y="13" width="5" height="5"/><rect x="22" y="13" width="5" height="5"/><rect x="6" y="21" width="5" height="5"/><rect x="14" y="21" width="5" height="5"/><rect x="22" y="21" width="5" height="5"/></g></svg>
</div>
<div class="abs cal-body">
  <span>1</span><span>2</span><span class="today">3</span><span>4</span><span>5</span><span>6</span><span>7</span>
  <span>8</span><span>9</span><span>10</span><span>11</span><span>12</span><span>13</span><span>14</span>
  <span>15</span><span>16</span><span>17</span><span>18</span><span>19</span><span>20</span><span>21</span>
  <span>22</span><span>23</span><span>24</span><span>25</span><span>26</span><span>27</span><span>28</span>
  <span>29</span><span>30</span><span class="off">1</span>
</div>

<div class="abs map" role="img" aria-label="Street map around the club location"></div>
<svg class="abs pin" width="56" height="130" viewBox="0 0 56 130"><path d="M28 0C12 0 0 12 0 28c0 20 28 52 28 52s28-32 28-52C56 12 44 0 28 0z" fill="#a6141e"/><circle cx="28" cy="27" r="11" fill="#fff"/></svg>

<div class="abs hours">
  <h3>Opening <b>Hours</b></h3>
  <ul>
    <li><span>▦</span><span>Monday</span><span>h. 6:00 - h. 24:00</span></li>
    <li><span>▦</span><span>Tuesday</span><span>h. 6:00 - h. 24:00</span></li>
    <li><span>▦</span><span>Wednesday</span><span>h. 6:00 - h. 24:00</span></li>
    <li><span>▦</span><span>Thursday</span><span>h. 6:00 - h. 24:00</span></li>
    <li><span>▦</span><span>Friday</span><span>h. 6:00 - h. 24:00</span></li>
    <li><span>▦</span><span>Saturday</span><span>h. 6:00 - h. 24:00</span></li>
    <li><span>▦</span><span>Sunday</span><span>h. 6:00 - h. 24:00</span></li>
  </ul>
  <p>Nam vestibulum, arcu sodales feugiat consectetur, nisl orci bibendum elit.</p>
  <p class="enjoy">Enjoy it!</p>
</div>

<footer class="abs footer"></footer>
<div class="abs news">
  <div class="f-h">NEWSLETTER SIGNUP</div>
  <p>Sign up for our newsletter<br>and get the latest news.</p>
  <div class="field">EMAIL ID</div>
  <div class="submit">SUBMIT ›</div>
</div>
<div class="abs f-brand"><i></i>IRONHOLD</div>
<div class="abs contact">
  <p>Lorem ipsum dolor sit amet, consectetur adipiscing elit. Nam viverra euismod odio, gravida pellentesque urna varius vitae. Sed dui lorem, adipiscing in</p>
  <div class="line" style="margin-top:22px">Phone: <em>1-800-555-0147</em></div>
  <div class="line">e-mail: <em>hello@ironholdclub.com</em></div>
</div>
<div class="abs menu">
  <div class="f-h">MENU</div>
  <ul><li>About</li><li>Trainers</li><li>Classes</li><li>Pricing</li><li>Privacy</li><li>Contact</li></ul>
</div>
<div class="abs community">
  <div class="f-h">COMMUNITY</div>
  <ul><li>Blog</li><li>Forum</li><li>Support</li><li>Newsletter</li></ul>
</div>
<div class="abs bottom">
  <span>© 2014 health &amp; fitness club All rights reserved</span>
  <span class="social"><span>kinwall</span><span>chirplo</span><span>snapvault</span></span>
</div>

</body>
</html>
```